BOLD & MINIMALIST DESIGN NEEDED

We want a very bold but minimalistic business card design that is impactful and utilizes both sides of the business card. Our current logo is included for your use.

We want bold fonts and good use of negative space. We don't want the logo to overpower the design.

Target Market(s)

Professionals who are building new commercial buildings.

Industry/Entity Type

Construction

Contact Information for Business Card

Name, Title, email, office phone, cell phone, website

Font styles to use
Serif
Sans Serif

Requirements
Must have
• Bold design!

```html
<!DOCTYPE html>
<html lang="en">
<head>
<meta charset="utf-8">
<title>Summitline Design + Build — Business Card</title>
<link rel="stylesheet" href="https://fonts.googleapis.com/css2?family=Oswald:wght@600;700&family=Montserrat:wght@400;500;700&display=swap">
<style>
  :root {
    --stage: #1b1b1b;
    --card-white: #ffffff;
    --card-dark: #232323;
    --accent: #8dc63f;
    --ink: #1a1a1a;
    --text-light: #f2f2f2;
  }
  * { box-sizing: border-box; margin: 0; padding: 0; }
  html, body {
    width: 1200px; height: 897px; overflow: hidden;
    background: var(--stage);
  }
  .canvas { position: relative; width: 1200px; height: 897px; }

  .card {
    position: absolute; left: 303px; width: 595px; height: 338px;
    border-radius: 22px; overflow: hidden;
    box-shadow: 0 8px 20px rgba(0,0,0,.5);
  }
  .card--front { top: 92px; background: var(--card-white); }
  .card--back  { top: 469px; background: var(--card-dark); }

  .front-swoosh { position: absolute; inset: 0; width: 100%; height: 100%; }

  .holder { position: absolute; left: 38px; top: 30px; }
  .holder__name {
    font-family: "Oswald", sans-serif; font-weight: 700;
    font-size: 31px; line-height: 1; letter-spacing: .2px;
    color: var(--accent); transform: scaleX(.92); transform-origin: left;
  }
  .holder__title {
    font-family: "Montserrat", sans-serif; font-weight: 500;
    font-size: 14px; color: var(--ink); margin-top: 4px; letter-spacing: .4px;
  }

  .brand {
    position: absolute; left: 345px; top: 88px; width: 220px;
    display: flex; align-items: center; justify-content: center; gap: 8px;
  }
  .brand__mark { width: 14px; height: 14px; background: var(--accent); flex: none; }
  .brand__name {
    font-family: "Montserrat", sans-serif; font-weight: 700;
    color: var(--ink); text-align: center; line-height: 1.05;
  }
  .brand__main { display: block; font-size: 27px; letter-spacing: .5px; }
  .brand__sub  { display: block; font-size: 11px; letter-spacing: 4px; margin-top: 4px; }

  .contacts {
    position: absolute; left: 37px; top: 228px; list-style: none;
    font-family: "Montserrat", sans-serif; font-weight: 400;
    font-size: 14px; color: var(--text-light);
  }
  .contacts li { display: flex; align-items: center; gap: 6px; height: 18px; }
  .contacts svg { width: 13px; height: 13px; flex: none; }
  .contacts .hl { color: var(--accent); }

  .back-pattern {
    position: absolute; inset: 0;
    background: linear-gradient(200deg, #4a4a4a 0%, #2c2c2c 45%, #1e1e1e 100%);
  }
  .back-brand {
    position: absolute; left: 0; right: 0; top: 180px; text-align: center;
    font-family: "Montserrat", sans-serif; font-weight: 700;
    font-size: 20px; letter-spacing: 1px; color: #ffffff;
  }
</style>
</head>
<body>
<main class="canvas">

  <section class="card card--front">
    <svg class="front-swoosh" viewBox="0 0 743 423" preserveAspectRatio="none" aria-hidden="true">
      <path d="M0 143 C 250 275, 500 316, 743 316 L743 423 L0 423 Z" fill="var(--card-dark)"/>
      <path d="M100 190 C 320 292, 540 286, 743 282 L743 306 C 520 307, 300 278, 100 190 Z" fill="var(--accent)"/>
      <path d="M100 192 C 300 284, 520 309, 743 309" fill="none" stroke="#ffffff" stroke-width="2.5"/>
    </svg>

    <div class="holder">
      <h1 class="holder__name">MARCUS RIDLEY</h1>
      <p class="holder__title">OWNER</p>
    </div>

    <div class="brand">
      <span class="brand__mark"></span>
      <p class="brand__name">
        <span class="brand__main">SUMMITLINE</span>
        <span class="brand__sub">DESIGN + BUILD</span>
      </p>
    </div>

    <ul class="contacts">
      <li>
        <svg viewBox="0 0 24 24" aria-hidden="true"><path fill="var(--accent)" d="M6.6 10.8a15.1 15.1 0 0 0 6.6 6.6l2.2-2.2c.3-.3.7-.4 1-.2 1.1.4 2.3.6 3.6.6.6 0 1 .4 1 1V20c0 .6-.4 1-1 1A17 17 0 0 1 3 4c0-.6.4-1 1-1h3.5c.6 0 1 .4 1 1 0 1.3.2 2.5.6 3.6.1.3 0 .7-.2 1z"/></svg>
        (555) 014-2287
      </li>
      <li>
        <svg viewBox="0 0 24 24" aria-hidden="true"><path fill="var(--accent)" d="M2 8c3-3 17-3 20 0v2.5h-5V8.5c-3-1-7-1-10 0v2H2z M6 11h12l3 8H3z"/><circle cx="12" cy="15" r="2.3" fill="var(--card-dark)"/></svg>
        (555) 014-2287
      </li>
      <li>
        <svg viewBox="0 0 24 24" aria-hidden="true"><rect x="2.5" y="5" width="19" height="14" rx="1.5" fill="none" stroke="var(--accent)" stroke-width="2"/><path d="M3 6l9 7 9-7" fill="none" stroke="var(--accent)" stroke-width="2"/></svg>
        summitlinebuild@mail.com
      </li>
      <li>
        <svg viewBox="0 0 24 24" aria-hidden="true"><g fill="none" stroke="var(--accent)" stroke-width="1.8"><circle cx="12" cy="12" r="9.5"/><ellipse cx="12" cy="12" rx="4.2" ry="9.5"/><path d="M2.5 12h19M4 7h16M4 17h16"/></g></svg>
        <span>www.<span class="hl">summitlinebuild</span>.com</span>
      </li>
    </ul>
  </section>

  <section class="card card--back">
    <div class="back-pattern" role="img" aria-label="Repeating embossed brand-mark pattern in dark greys, fading lighter toward the top right"></div>
    <p class="back-brand">SUMMITLINE</p>
  </section>

</main>
</body>
</html>
```